Pictorama Business Card For Comedian

Hi,

I'd like a 2-sided business card that kind mimics an Pictorama page. I've attached screenshots with the copy and language that should be written on there.

I'd like it to be way more stylized and a bit more creative than what I did on Powerpoint. I just did a mockup so that you can have an idea. I'd like it to be designed and you to take a bit of creative imagery so that it doesn't look so static and monochromatic.

PLEASE BE CREATIVE WITH THESE DESIGNS. I DON'T WANT IT TO LOOK EXACTLY LIKE THE ATTACHED IMAGE OR EXACTLY LIKE AN PICTORAMA PAGE. I want to use it as inspiration to create something that looks more sleek, and creative. I don't want the colors to just be boring gray, and blue. Have fun and spice it up a bit!

Check out my website MauraVelinski.com to see the colors and fonts I use for my branding.

For the main photo: Here's a link with the hi-res photo: !https://www.filecrate.net/s/q8x4tmbw2rzplkd/Maura-Velinski-C73K2251.jpg?dl=0

For the thumbnail icon photo, you can use this: https://www.filecrate.net/s/vh5ntrx9gqwmyle/Maura%20Velinski%20Tide%20Glass%20Headshot.jpg?dl=0

Use the Standard Business Card Template from Prinzo.com:
https://help.prinzo.com/hc/en-us/article_attachments/318842907/Standard_Size__US__Business_Cards_Portrait.jpg

Please let me know if you have any questions.

Industry/Entity Type

Business

Contact Information for Business Card

All of the text and copy has been provided on the attached jpg.

Colors
33a6d7
0255a3
aaaaaa
dbdbdb
1b1b1b

Requirements
Should not have
• A Hyperlink for the Email Addresses

```html
<!DOCTYPE html>
<html lang="en">
<head>
<meta charset="utf-8">
<title>Pictorama Business Card – Maura Velински</title>
<link rel="stylesheet" href="https://fonts.googleapis.com/css2?family=Source+Sans+3:wght@400;600;700&display=swap">
<style>
  :root{
    --page:#f1f1f1;
    --card:#1b1b1b;
    --card-deep:#121212;
    --accent:#33a6d7;
    --accent-deep:#0255a3;
    --text:#ffffff;
    --muted:#dbdbdb;
    --label:#1b1b1b;
  }
  *{box-sizing:border-box;margin:0;padding:0}
  html,body{width:1200px;height:1200px;overflow:hidden}
  body{background:var(--page);font-family:"Source Sans 3",sans-serif;position:relative}
  .side-label{position:absolute;top:212px;font-size:35px;font-weight:400;color:var(--label);letter-spacing:.5px;line-height:1}
  .side-label--front{left:117px}
  .side-label--back{left:677px}
  .card{position:absolute;top:266px;width:395px;height:668px;background:radial-gradient(ellipse at 50% 40%,#262626 0%,var(--card) 55%,var(--card-deep) 100%);color:var(--text)}
  .card--front{left:117px}
  .card--back{left:677px}
  .accent-bar{position:absolute;left:15px;width:8px;background:var(--accent)}
  .card--front .accent-bar{top:14px;height:408px}
  .card--back .accent-bar{top:14px;height:626px}
  .t{position:absolute;line-height:1;white-space:nowrap}

  /* front */
  .avatar{position:absolute;background:linear-gradient(160deg,#3a2a22,#7a4a35 55%,#c29a55);}
  .avatar--header{left:40px;top:34px;width:45px;height:45px}
  .handle{left:98px;top:35px;font-size:20px;font-weight:700}
  .location{left:98px;top:56px;font-size:20px;color:var(--accent)}
  .hero{position:absolute;left:43px;top:139px;width:307px;height:307px;border-radius:50%;border:4px solid #fff;background:radial-gradient(circle at 50% 45%,#6b3f2a 0%,#3c2419 35%,#1c1512 65%,#d8d2cc 100%);box-shadow:0 0 10px rgba(0,0,0,.6)}
  .actions{position:absolute;left:34px;top:476px;width:340px;height:22px}
  .likes-icon{position:absolute;left:37px;top:528px}
  .likes{left:61px;top:528px;font-size:14px;color:var(--muted)}
  .caption{position:absolute;left:28px;top:550px;width:360px;font-size:13.6px;line-height:18.4px;color:var(--muted);letter-spacing:-.1px;white-space:nowrap}
  .caption strong{color:var(--text);font-weight:700}

  /* back */
  .section-title{left:0;width:395px;text-align:center;top:29px;font-size:20px;font-weight:700;color:var(--accent)}
  .info-icon{position:absolute;left:35px}
  .info{left:69px;font-size:14px;color:var(--muted)}
  .avatar--edit{left:305px;top:99px;width:53px;height:53px}
  .edit-link{left:305px;width:53px;text-align:center;top:156px;font-size:12px;color:var(--accent)}
  .heading{left:34px;font-size:18px;color:var(--accent)}
  .body{left:34px;font-size:13.4px;color:var(--muted)}
  .signoff{left:0;width:395px;text-align:center;top:580px;font-size:20px;color:var(--text)}
</style>
</head>
<body>
  <div class="side-label side-label--front">FRONT</div>
  <div class="side-label side-label--back">BACK</div>

  <section class="card card--front">
    <div class="accent-bar"></div>
    <div class="avatar avatar--header" role="img" aria-label="Thumbnail profile photo of Maura Velински"></div>
    <div class="t handle">glamwit</div>
    <div class="t location">Brooklyn, New York</div>
    <div class="hero" role="img" aria-label="Main headshot photo of Maura Velински"></div>

    <svg class="actions" viewBox="0 0 340 22" aria-hidden="true">
      <path d="M10 19 L2 10.5 A4.6 4.6 0 0 1 10 4.5 A4.6 4.6 0 0 1 18 10.5 Z" fill="var(--accent)"/>
      <path d="M45 18 l-2 3 l1-4.2 A8 8 0 1 1 45 18 Z" fill="none" stroke="var(--accent)" stroke-width="1.6"/>
      <path d="M74 19 C74 11 79 8 90 8 M85 3 l5 5 l-5 5" fill="none" stroke="var(--accent)" stroke-width="1.6" stroke-linecap="round" stroke-linejoin="round"/>
      <circle cx="306" cy="11" r="3.3" fill="none" stroke="var(--accent)" stroke-width="1.4"/>
      <circle cx="318" cy="11" r="3.3" fill="none" stroke="var(--accent)" stroke-width="1.4"/>
      <circle cx="330" cy="11" r="3.3" fill="none" stroke="var(--accent)" stroke-width="1.4"/>
    </svg>
    <svg class="likes-icon" width="16" height="14" viewBox="0 0 16 14" aria-hidden="true">
      <path d="M8 13.5 L1.2 6.6 A3.8 3.8 0 0 1 8 2.4 A3.8 3.8 0 0 1 14.8 6.6 Z" fill="var(--accent)"/>
    </svg>
    <div class="t likes">321 LIKES</div>
    <p class="caption"><strong>glamwit</strong> Your favorite comic’s favorite comic. #ISAIDIT<br>#SOITSTRUE #FINDME #FOLLOWME #NOTTOMYHOUS<br>#POSTABOUTMEUDINGTHESEHASHTAGS #MAURAVELINSKI<br>#GLAMWIT #IMSUCHABROOKLYNGIR<br>#MAKENYUNSAFEAGAIN #BROOKLYNSTANDUPCOMEDY</p>
  </section>

  <section class="card card--back">
    <div class="accent-bar"></div>
    <div class="t section-title">EDIT PROFILE</div>

    <svg class="info-icon" style="top:107px" width="18" height="18" viewBox="0 0 18 18" aria-hidden="true">
      <circle cx="9" cy="5" r="4" fill="var(--text)"/>
      <path d="M1 18 C1 11 17 11 17 18 Z" fill="var(--text)"/>
    </svg>
    <div class="t info" style="top:110px">MAURA VELИНСКИ</div>

    <svg class="info-icon" style="top:135px" width="19" height="19" viewBox="0 0 20 20" aria-hidden="true">
      <g fill="none" stroke="var(--text)" stroke-width="1.3">
        <circle cx="10" cy="10" r="8.5"/><ellipse cx="10" cy="10" rx="4" ry="8.5"/>
        <path d="M1.5 10 H18.5 M3 5.5 H17 M3 14.5 H17"/>
      </g>
    </svg>
    <div class="t info" style="top:138px">WWW.MAURAVELINSKI.COM</div>

    <div class="t info" style="top:166px">For Booking:</div>
    <svg class="info-icon" style="top:185px" width="20" height="15" viewBox="0 0 20 15" aria-hidden="true">
      <g fill="none" stroke="var(--text)" stroke-width="1.3"><rect x="1" y="1" width="18" height="13"/><path d="M1 1 L10 9 L19 1 M1 14 L7.5 7 M19 14 L12.5 7"/></g>
    </svg>
    <div class="t info" style="top:184px">Nadia@HalvessaTalentGroup.com</div>
    <div class="t info" style="top:202px">Jess.Morrow@qorvelt.com</div>

    <div class="avatar avatar--edit" role="img" aria-label="Thumbnail profile photo of Maura Velински"></div>
    <div class="t edit-link">EDIT</div>

    <div class="t heading" style="top:256px">ABOUT</div>
    <div class="t body" style="top:284px">Stand Up Comedian. I Host. I Write. I Act. I Dance. I</div>
    <div class="t body" style="top:304px">Do Not Sing Unless I’m in the Shower. I acceot Tips.</div>
    <div class="t body" style="top:325px">(Not on jokes, but on Zeltip)</div>
    <div class="t body" style="top:366px">As seen on Qorvin, Jestwell Central, Zantu, Trovik TV,</div>
    <div class="t body" style="top:386px">Brume, and Ovelo.</div>

    <div class="t heading" style="top:439px">MORE INFO</div>
    <div class="t body" style="top:473px">KINDRELLO.COM/MAURAVELINSKI</div>
    <div class="t body" style="top:493px">QUILLCAST.COM/GLAMWIT</div>
    <div class="t body" style="top:514px">PICTORAMA.COM/GLAMWIT</div>

    <div class="t signoff">Let’s Stay Connected</div>
  </section>
</body>
</html>
```